Beacon Advisory Website

I currently have a website www.beaconadvisoryinc.com. We are a IT Consulting Company. Our website will pretty much tell out our services. I am looking to enhance my website and make it look more professional. Looking for very classy and Contemporary look and design for my website.

It Company

```html
<!DOCTYPE html>
<html lang="en">
<head>
<meta charset="utf-8">
<title>Beacon Advisory</title>
<link href="https://fonts.googleapis.com/css2?family=Open+Sans:wght@300;400;600;700&display=swap" rel="stylesheet">
<style>
:root{
  --brand:#1b5ea8;
  --brand-light:#2a7bc4;
  --ink:#333;
  --muted:#777;
  --band-deep:#0f6cab;
  --band-light:#3aa0d8;
  --tile:#222;
  --soft:#f4f5f6;
  --footer:#3b3b3b;
  --white:#fff;
}
*{margin:0;padding:0;box-sizing:border-box}
html,body{width:742px;height:1200px;overflow:hidden;background:var(--white)}
body{position:relative;font-family:"Open Sans",Arial,sans-serif;color:var(--ink)}
.abs{position:absolute}
.top-rule{left:0;top:0;width:742px;height:2px;background:var(--brand-light)}
.header{left:0;top:2px;width:742px;height:64px;border-bottom:1px solid #e6e6e6}
.brand{left:62px;top:19px;display:flex;align-items:center;gap:7px}
.brand-mark{width:26px;height:26px;background:var(--brand)}
.brand-name{font-size:15px;font-weight:700;color:var(--brand);letter-spacing:.3px}
.nav{right:62px;top:29px;display:flex;gap:17px;font-size:7px;color:#333;list-style:none;align-items:center}
.nav .active{color:var(--brand-light)}
.hero{left:0;top:66px;width:742px;height:310px;background:linear-gradient(110deg,#c9a08a 0%,#dfe3e6 30%,#e9eef2 55%,#d7e1e8 100%)}
.hero-arrow{top:202px}
.section-title{width:742px;text-align:center;font-size:17px;font-weight:400;color:var(--ink)}
.section-title span{color:var(--brand)}
.title-rule{left:350px;width:43px;height:1px;background:#555}
.lead{width:742px;text-align:center;font-size:6.5px;line-height:14.5px;color:var(--muted)}
.services{left:0;top:508px;width:742px;height:275px;background:radial-gradient(ellipse at 30% 30%,var(--band-light),var(--band-deep) 70%)}
.services .section-title,.services .lead{color:var(--white)}
.service{width:150px;text-align:center;color:var(--white)}
.service-tile{width:77px;height:77px;margin:0 auto;background:var(--tile);display:flex;align-items:center;justify-content:center}
.service-tile.active{background:var(--brand)}
.service h3{font-size:9px;font-weight:400;margin-top:10px}
.service p{font-size:7px;line-height:13.7px;margin-top:4px}
.solution{width:190px;text-align:center}
.solution-photo{width:190px;height:105px;border:3px solid var(--white);box-shadow:0 3px 6px rgba(0,0,0,.25)}
.solution h3{font-size:11px;font-weight:400;margin-top:14px;color:var(--ink)}
.solution h3.active{color:var(--brand)}
.testimonial{left:0;top:1034px;width:742px;height:113px;background:var(--soft)}
.quote{left:175px;top:1025px;width:490px;font-size:6.5px;line-height:14.5px;color:var(--muted)}
.author{left:175px;top:1114px;font-size:6.5px;line-height:12px}
.author b{color:var(--brand);font-weight:400;display:block}
.footer{left:0;top:1147px;width:742px;height:53px;background:var(--footer);color:var(--white)}
.footer-nav{left:62px;top:1158px;font-size:6.5px;color:var(--white);list-style:none;display:flex;gap:8px}
.copyright{left:62px;top:1177px;font-size:6.5px;color:var(--white)}
.social{left:600px;top:1165px;display:flex;gap:4px}
.social span{width:17px;height:17px;border-radius:50%;background:#666}
</style>
</head>
<body>
<div class="abs top-rule"></div>
<header class="abs header"></header>
<div class="abs brand"><div class="brand-mark"></div><div class="brand-name">Beacon Advisory</div></div>
<ul class="abs nav">
  <li class="active">HOME</li><li>COMPANY</li><li>SERVICES</li><li>SOLUTIONS</li><li>RESOURCES</li><li>CAREER</li><li>CONTACT US</li>
  <li><svg width="8" height="8" viewBox="0 0 8 8"><circle cx="3.2" cy="3.2" r="2.4" fill="none" stroke="#1b5ea8" stroke-width="1.2"/><line x1="5" y1="5" x2="7.5" y2="7.5" stroke="#1b5ea8" stroke-width="1.3"/></svg></li>
</ul>

<div class="abs hero" role="img" aria-label="Hands holding a tablet showing the company website"></div>
<svg class="abs hero-arrow" style="left:28px" width="10" height="36" viewBox="0 0 10 36"><polyline points="9,1 1,18 9,35" fill="none" stroke="#fff" stroke-width="1"/></svg>
<svg class="abs hero-arrow" style="left:704px" width="10" height="36" viewBox="0 0 10 36"><polyline points="1,1 9,18 1,35" fill="none" stroke="#fff" stroke-width="1"/></svg>

<h1 class="abs section-title" style="left:0;top:393px"><span>Welcome To</span> Our Company</h1>
<div class="abs title-rule" style="top:426px"></div>
<p class="abs lead" style="left:0;top:438px">Today's IT market is a dynamic, fast-paced industry, with ever-increasing demands. Meeting these demands for over 25 years, Beacon Advisory maintains a global presence, aggressively<br>recruiting expertly qualified IT and Management Professionals from around the world and cultivating key partnerships with corporations to understand their business models<br>end-to-end, with a goal of delivering exceptional client service and ensuring a consistent delivery of the talent needed to drive results.</p>

<section class="abs services">
  <h2 class="abs section-title" style="left:0;top:12px">Our Services</h2>
  <p class="abs lead" style="left:0;top:58px;font-size:7px">Beacon Advisory Training programs are perfect for individuals to enhance their careers. Our hands-on practical and interactive programs</p>

  <div class="abs service" style="left:53px;top:99px">
    <div class="service-tile active"><svg width="30" height="26" viewBox="0 0 30 26"><rect x="2" y="2" width="26" height="16" rx="1" fill="none" stroke="#fff" stroke-width="2.5"/><rect x="13" y="18" width="4" height="4" fill="#fff"/><rect x="9" y="22" width="12" height="2" fill="#fff"/></svg></div>
    <h3>Technology</h3>
    <p>Beacon Advisory provides training choices in multiple formats and delivery methods, offering top-quality training custom-tailored</p>
  </div>
  <div class="abs service" style="left:214px;top:99px">
    <div class="service-tile"><svg width="30" height="26" viewBox="0 0 30 26"><rect x="10" y="2" width="10" height="5" fill="none" stroke="#fff" stroke-width="2"/><rect x="1" y="6" width="28" height="19" rx="2" fill="#fff"/><rect x="1" y="13" width="28" height="2" fill="#222"/><rect x="13" y="12" width="4" height="4" fill="#fff"/></svg></div>
    <h3>Business</h3>
    <p>Beacon Advisory provides training choices in multiple formats and delivery methods, offering top-quality training custom-tailored</p>
  </div>
  <div class="abs service" style="left:376px;top:99px">
    <div class="service-tile"><svg width="30" height="28" viewBox="0 0 30 28"><path d="M16 4H4v22h22V14" fill="none" stroke="#fff" stroke-width="2.5"/><path d="M25 2l3 3-12 12-4 1 1-4z" fill="#fff"/></svg></div>
    <h3>Application</h3>
    <p>Beacon Advisory provides training choices in multiple formats and delivery methods, offering top-quality training custom-tailored</p>
  </div>
  <div class="abs service" style="left:538px;top:99px">
    <div class="service-tile"><svg width="30" height="30" viewBox="0 0 30 30"><polygon points="15,1 27,8 27,22 15,29 3,22 3,8" fill="none" stroke="#fff" stroke-width="1.8"/><polygon points="15,7 22,19 8,19" fill="none" stroke="#fff" stroke-width="1.5"/><polygon points="15,23 8,11 22,11" fill="none" stroke="#fff" stroke-width="1.5"/></svg></div>
    <h3>Development</h3>
    <p>Beacon Advisory provides training choices in multiple formats and delivery methods, offering top-quality training custom-tailored</p>
  </div>
</section>

<h2 class="abs section-title" style="left:0;top:800px"><span>Our</span> Solution</h2>
<div class="abs title-rule" style="top:831px"></div>
<p class="abs lead" style="left:0;top:843px;font-size:7px">Our proven implementation and audit models allow for capturing requirements while expediting the process.</p>

<div class="abs solution" style="left:62px;top:877px">
  <div class="solution-photo" role="img" aria-label="Hand touching a dashboard of charts" style="background:linear-gradient(135deg,#2c4d6e,#6f93b3 60%,#c9d6e0)"></div>
  <h3 class="active">Dashboards</h3>
</div>
<div class="abs solution" style="left:275px;top:877px">
  <div class="solution-photo" role="img" aria-label="Data warehousing illustration on a blue world map" style="background:linear-gradient(135deg,#1a6fc0,#2f8ad6 60%,#1a62ad)"></div>
  <h3>Data Warehousing</h3>
</div>
<div class="abs solution" style="left:490px;top:877px">
  <div class="solution-photo" role="img" aria-label="Gears with business process icons" style="background:linear-gradient(135deg,#dfe6ec,#8ea4b8 50%,#3b5f86)"></div>
  <h3>Business Process Management</h3>
</div>

<section class="abs testimonial"></section>
<div class="abs" role="img" aria-label="Portrait of the quoted executive" style="left:70px;top:1051px;width:74px;height:74px;border-radius:50%;background:radial-gradient(circle,#e3cfc3,#9fb3c4)"></div>
<div class="abs" style="left:160px;top:1047px;font-size:18px;color:#ccc;line-height:1">&ldquo;</div>
<div class="abs" style="left:646px;top:1085px;font-size:18px;color:#ccc;line-height:1">&rdquo;</div>
<p class="abs quote" style="top:1057px">Lorem Ipsum es simplemente el texto de relleno de las imprentas y archivos de texto. Lorem Ipsum ha sido el texto de relleno estándar de las industrias desde el año 1500, cuando un impresor (N. del T. persona que se dedica a la imprenta) desconocido usó una galería On the other hand, we denounce moment, so blinded by desire, that they cannot foresee...</p>
<div class="abs author"><b>MARTIN HALE</b>Marketing Executive</div>

<footer class="abs footer"></footer>
<ul class="abs footer-nav">
  <li>HOME</li><li>/</li><li>COMPANY</li><li>/</li><li>SERVICES</li><li>/</li><li>SOLUTIONS</li><li>/</li><li>RESOURCES</li><li>/</li><li>CAREER</li><li>/</li><li>CONTACT US</li>
</ul>
<p class="abs copyright">2016 © Copy right Beacon Advisory all right reserved</p>
<div class="abs social"><span></span><span></span><span></span><span></span></div>
</body>
</html>
```